Coral Slumber Depot Website

Need a design for a local Miami mattress store.
The store is called Coral Slumber Depot.
need it to be something that customers can find on the internet and will
give them my location, they need to know i have the same brand mattress as the other store except i have them at almost half the price.

the office phone number is (786)413-9067
the office address is: 24517 sw Heron Glade Ln, Miami FL 33189

included is the logo, id like to stick the with white and teal design

here are is an excerpt that can or cannot be included

"We are a premium mattress discount outlet store located in South Florida; offering Free Delivery to Broward Miami-Dade, the Keys, and Palm Beach.

We carry the best brands in the market: Kellard DreamLoft; Brodin SpineEase, Whitcombe & Lyle, Pardue, among others.

We are open 7 days a week, and we are accessible from all major highways. We are a family business and our goal is to provide you with the most comfortable and best quality mattress at a price that has no competition. Come visit us and take a look at our large inventory selection."

```html
<!DOCTYPE html>
<html lang="en">
<head>
<meta charset="utf-8">
<title>Coral Slumber Depot</title>
<link href="https://fonts.googleapis.com/css2?family=Federo&family=Arvo:wght@700&family=Arimo:wght@400;700&display=swap" rel="stylesheet">
<style>
:root{
  --navy:#0b5b8b;
  --teal:#17a9c9;
  --teal-soft:#5fc1d6;
  --ink:#3a3a3a;
  --grey:#5a5a5a;
  --panel:#ededed;
  --white:#ffffff;
}
*{margin:0;padding:0;box-sizing:border-box}
html,body{width:790px;height:1200px;overflow:hidden;background:var(--white);font-family:"Arimo",Arial,sans-serif;color:var(--ink)}
.page{position:relative;width:790px;height:1200px}
.masthead{position:absolute;left:0;top:0;width:790px;height:93px;background:linear-gradient(#ffffff,#ececec)}
.brand{position:absolute;left:0;right:0;top:36px;text-align:center;font-family:"Federo",sans-serif;font-size:26px;color:#4a4a4a;letter-spacing:1px}
.brand-mark{display:inline-block;width:10px;height:10px;background:var(--teal);margin-right:8px;vertical-align:middle}
.nav{position:absolute;left:0;top:93px;width:790px;height:28px;background:var(--navy);display:flex;justify-content:center;align-items:center}
.nav a{color:var(--white);font-size:9.5px;text-decoration:none;padding:0 15px;height:16px;line-height:16px;border-right:1px solid rgba(255,255,255,.2)}
.nav a:last-child{border-right:none}
.nav a.active{background:var(--white);color:#222;padding:0 4px;margin-right:11px;border-radius:2px}
.nav-rule{position:absolute;left:0;top:121px;width:790px;height:7px;background:#d5d9dc}
.hero{position:absolute;left:0;top:128px;width:790px;height:344px;background:linear-gradient(115deg,#2f88b7 0%,#4aa3cc 40%,#2a7fb0 70%,#145f92 100%)}
.hero svg{position:absolute;left:0;top:0}
.slide{position:absolute;left:67px;top:19px;width:656px;height:285px;border:3px solid var(--teal);background:linear-gradient(#f6f6f4,#e9e6e0)}
.slide-photo{position:absolute;inset:0;background:linear-gradient(160deg,#f4f3ef 0%,#e8e3d8 45%,#9fc5cc 60%,#f2efe8 75%,#ddd8cc 100%)}
.slide-caption{position:absolute;left:8px;top:188px;font-family:"Arvo",serif;color:#111;letter-spacing:2px}
.slide-caption .l1{display:inline-block;background:rgba(60,60,60,.75);color:var(--white);font-size:25px;padding:0 24px 0 4px;line-height:30px}
.slide-caption .l2{display:block;background:rgba(255,255,255,.7);font-size:25px;padding:4px 16px 0 4px;line-height:30px;margin-top:4px}
.dots{position:absolute;left:369px;top:317px;display:flex;gap:4px}
.dots span{width:8px;height:8px;border-radius:50%;background:var(--white)}
.intro-title{position:absolute;left:70px;top:500px;width:660px;font-family:"Federo",sans-serif;color:var(--teal);font-size:14.5px;line-height:20px;letter-spacing:1px}
.intro-copy{position:absolute;left:70px;top:549px;width:650px;font-size:8.6px;line-height:13.2px;color:var(--grey)}
.promo{position:absolute;left:66px;top:660px;width:461px;height:228px;background:linear-gradient(135deg,#6a9fb4,#3f7a94 60%,#5e92a8)}
.promo p{position:absolute;left:15px;top:88px;width:430px;color:var(--white);font-weight:700;font-size:15px;line-height:24px}
.office{position:absolute;left:552px;top:660px;width:173px;height:229px;border:1px solid #d0d0d0;background:var(--white)}
.office-map{position:absolute;left:4px;top:4px;width:163px;height:81px;background:linear-gradient(135deg,#f1ead2,#e9dca0 50%,#cfd8dd)}
.office h3{position:absolute;left:4px;top:93px;width:163px;height:21px;background:var(--navy);color:var(--white);font-size:12.8px;line-height:21px;padding-left:3px;letter-spacing:.3px}
.office address{position:absolute;left:6px;top:125px;font-style:normal;font-size:11.5px;line-height:12px;color:#444}
.office .tel{position:absolute;left:8px;top:155px;font-size:11.5px;color:#444}
.office .spot{position:absolute;left:15px;top:183px;background:#444;color:var(--white);font-size:11px;padding:3px 7px;text-decoration:none}
.brands-title{position:absolute;left:67px;top:922px;font-family:"Federo",sans-serif;color:var(--teal);font-size:14.5px;letter-spacing:1px}
.brands{position:absolute;left:66px;top:950px;width:660px;height:102px;background:var(--panel);border:1px solid #dcdcdc}
.brands svg.arrow{position:absolute;top:34px}
.brand-tile{position:absolute;top:17px;width:133px;height:67px;border:3px solid var(--white);display:flex;align-items:center;justify-content:center;text-align:center;font-weight:700;font-size:13px;line-height:15px}
.t1{left:40px;background:#c0102b;color:var(--white)}
.t2{left:187px;background:#f0d9ab;color:#3b2a10}
.t3{left:334px;background:#a9a9a9;color:#333}
.t4{left:481px;background:#e7f3fb;color:#1a3f80}
.footer{position:absolute;left:0;top:1081px;width:790px;height:119px;background:var(--navy);color:var(--white)}
.footer h4{font-family:"Federo",sans-serif;font-weight:400;font-size:14px;letter-spacing:1px;position:absolute;top:10px}
.hours{position:absolute;left:70px;top:30px;font-size:9.5px;line-height:13.2px}
.col-rule{position:absolute;top:10px;width:1px;height:105px;background:rgba(255,255,255,.12)}
.faddr{position:absolute;left:213px;top:30px;font-size:9.5px;line-height:18px}
.social{position:absolute;left:407px;top:32px;width:150px;display:grid;grid-template-columns:repeat(3,auto);gap:3px 4px;font-size:8.5px}
.social span{background:rgba(255,255,255,.15);padding:2px 3px}
.copy{position:absolute;left:583px;top:14px;font-size:8.8px;line-height:13.5px;color:#d8e6ef}
.legal{position:absolute;right:70px;top:92px;font-size:9px;font-weight:700}
.legal a{color:var(--white);text-decoration:none}
.legal i{font-style:normal;margin:0 7px}
</style>
</head>
<body>
<div class="page">
  <header class="masthead">
    <div class="brand"><span class="brand-mark"></span>Coral Slumber Depot</div>
  </header>
  <nav class="nav">
    <a class="active">HOME</a><a>WE ARE MATTRESS</a><a>DISCOUNTERS</a><a>LOCATION</a><a>GET IN TOUCH</a>
  </nav>
  <div class="nav-rule"></div>

  <section class="hero">
    <svg width="790" height="344" viewBox="0 0 790 344">
      <path d="M0 190 C200 120 420 250 790 160 L790 344 L0 344Z" fill="#1e6fa3" opacity=".35"/>
      <path d="M0 300 C250 240 500 330 790 260" stroke="#7cc3e0" stroke-width="3" fill="none" opacity=".6"/>
    </svg>
    <div class="slide">
      <div class="slide-photo" role="img" aria-label="White mattress dressed with teal and gold pillows and a teal throw"></div>
      <div class="slide-caption"><span class="l1">COMFORTABLE</span><span class="l2">HIGH QUALITY MATTRES</span></div>
    </div>
    <div class="dots"><span></span><span></span><span></span></div>
  </section>

  <h2 class="intro-title">WE ARE A FAMILY BUSINESS AND OUR GOAL IS TO PROVIDE YOU WITH THE MOST COMFORTABLE AND BEST QUALITY MATTRESS AT A PRICE THAT HAS NO COMPETITION</h2>
  <p class="intro-copy">Lorem ipsum dolor sit amet, consectetur adipisicing elit, sed do eiusmod tempor incididunt ut labore et dolore magna aliqua. Ut enim ad minim veniam, quis nostrud exercitation ullamco laboris nisi ut aliquip ex ea commodo consequat. Duis aute irure dolor in reprehenderit in voluptate velit esse cillum dolore eu fugiat nulla pariatur. Excepteur sint occaecat cupidatat non proident, sunt in culpa qui officia deserunt mollit anim id est laborum.Lorem ipsum dolor sit amet, consectetur adipisicing elit, sed do eiusmod tempor incididunt ut labore et dolore magna aliqua. Ut enim ad minim veniam, quis nostrud exercitation ullamco laboris nisi ut aliquip ex ea commodo consequat. Duis aute irure dolor in reprehenderit in voluptate velit esse cillum dolore eu fugiat nulla pariatur. Excepteur sint occaecat cupidatat non proident, sunt in culpa qui officia deserunt mollit anim id est laborum.</p>

  <section class="promo" role="img" aria-label="Bedroom with a dressed bed and a plant, tinted blue">
    <p>WE ARE A PREMIUM MATTRESS DISCOUNT OUTLET STORE LOCATED IN SOUTH FLORIDA; OFFERING FREE DELIVERY TO BROWARD MIAMI-DADE, THE KEYS, AND</p>
  </section>

  <aside class="office">
    <div class="office-map" role="img" aria-label="Street map around the store location"></div>
    <h3>THE OFFICE ADDRESS:</h3>
    <address>24517 sw Heron Glade Ln<br>&nbsp;Miami FL 33189</address>
    <div class="tel">Tel: (786)413-9067</div>
    <a class="spot">Spot Us ››</a>
  </aside>

  <h2 class="brands-title">WE CARRY THE BEST BRANDS IN THE MARKET</h2>
  <section class="brands">
    <svg class="arrow" style="left:12px" width="18" height="30" viewBox="0 0 18 30"><path d="M16 2 L3 15 L16 28" stroke="#b5b5b5" stroke-width="4" fill="none"/></svg>
    <div class="brand-tile t1">Kellard<br>DreamLoft</div>
    <div class="brand-tile t2">Whitcombe<br>&amp; Lyle</div>
    <div class="brand-tile t3">Pardue<br>Furniture</div>
    <div class="brand-tile t4">Brodin<br>SpineEase</div>
    <svg class="arrow" style="left:630px" width="18" height="30" viewBox="0 0 18 30"><path d="M2 2 L15 15 L2 28" stroke="#b5b5b5" stroke-width="4" fill="none"/></svg>
  </section>

  <footer class="footer">
    <h4 style="left:66px">STORE HOURS</h4>
    <div class="hours">Mon. 9 a.m - 5 p.m<br>Tue.&nbsp; 9 a.m - 5 p.m<br>Wed. 9 a.m - 5 p.m<br>Thu.&nbsp; 9 a.m - 5 p.m<br>Fri.&nbsp;&nbsp;&nbsp; 9 a.m - 5 p.m<br>Sat.&nbsp; 9 a.m - 5 p.m</div>
    <div class="col-rule" style="left:188px"></div>
    <h4 style="left:213px">OFFICE ADDRESS</h4>
    <div class="faddr">24517 sw Heron Glade Ln,<br>&nbsp;Miami FL 33189 (786)413-9067</div>
    <div class="col-rule" style="left:383px"></div>
    <h4 style="left:407px">FOLLOW US</h4>
    <div class="social"><span>Friendnest</span><span>Chirpline</span><span>Workweave</span><span>Clipcast</span><span>Circlepost</span><span>Pinboardly</span></div>
    <div class="col-rule" style="left:561px;height:70px"></div>
    <div class="copy">© 2014 Copyright - Coral Slumber Depot.<br>&nbsp;All rights reserved</div>
    <div class="legal"><a>Home</a><i>I</i><a>Newsletter</a><i>I</i><a>Press</a><i>I</i><a>Contact Us</a><i>I</i><a>Terms of Use</a><i>I</i><a>Credits</a></div>
  </footer>
</div>
</body>
</html>
```